New business stationairy

I need paper with header and footer and business cards.
I am a Ltd Company and my main field of expertise is QA/QC inspection in the Oil and Gas Industry. I will need all contact detail inserted and a footer with registration number and bank details etc

```html
<!DOCTYPE html>
<html lang="en">
<head>
<meta charset="utf-8">
<title>Harland Inspection Services Ltd – Letterhead</title>
<link href="https://fonts.googleapis.com/css2?family=Montserrat:wght@400;600;700&display=swap" rel="stylesheet">
<style>
  :root {
    --backdrop: #ececec;
    --paper: #fbfbfb;
    --slate: #666a78;
    --slate-light: #a9abb3;
    --teal: #1684ad;
    --ink: #55585f;
  }
  * { box-sizing: border-box; margin: 0; padding: 0; }
  html, body {
    width: 1200px; height: 936px; overflow: hidden;
    background: var(--backdrop);
    font-family: "Montserrat", Arial, sans-serif;
  }
  .letterhead {
    position: absolute; left: 300px; top: 44px;
    width: 600px; height: 848px;
    background: var(--paper);
    box-shadow: 0 2px 10px rgba(0,0,0,0.12);
  }
  .top-band {
    position: absolute; left: 0; top: 0; width: 100%; height: 8px;
    background: var(--slate-light);
  }
  .company-name {
    position: absolute; left: 48px; top: 70px;
    font-size: 15px; font-weight: 600; letter-spacing: 0.3px;
    color: var(--teal); white-space: nowrap;
  }
  .footer-contact {
    position: absolute; left: 30px; bottom: 24px;
    font-size: 7px; line-height: 1.4; color: var(--ink);
  }
  .footer-contact .label { color: var(--teal); font-weight: 700; }
  .footer-company {
    position: absolute; right: 30px; bottom: 24px;
    font-size: 7px; line-height: 1.4; color: var(--ink);
    text-align: right; text-transform: uppercase;
  }
  .footer-company .reg { text-transform: none; }
  .footer-bands {
    position: absolute; left: 0; bottom: 0; width: 600px; height: 14px;
  }
</style>
</head>
<body>
  <main class="letterhead">
    <div class="top-band"></div>

    <header>
      <p class="company-name">Harland Inspection Services Ltd</p>
    </header>

    <footer>
      <div class="footer-contact">
        <p>The Willows, Mill Lane, Ashby, Marlow Vale, Kent, KT4 9RL</p>
        <p><span class="label">Phone:</span> +07700 900412 &nbsp;<span class="label">Email:</span> office@harlandinspect.co.uk</p>
      </div>
      <div class="footer-company">
        <p>Harland Inspection Services Ltd</p>
        <p class="reg">Company registration No: 8142675</p>
      </div>
      <svg class="footer-bands" viewBox="0 0 600 14" width="600" height="14">
        <polygon points="0,0 338,0 330,14 0,14" fill="var(--slate)"/>
        <polygon points="342,0 600,0 600,14 334,14" fill="var(--teal)"/>
      </svg>
    </footer>
  </main>
</body>
</html>
```